Business Card and Letterhead for Pimlu - modern real estate business

I need a double sided business card design for Pimlu. Please see business card brief here https://files.trelvonadocs.com/sheet/r/7QzTmWbaXLJnoPEd-kRyUgFhHsstbvCe2qfoMxDa_pz/view?mode=shared

Please feel free to design the business cards however you feel best. I am happy to give some creative freedoms and then provide feedback from there.

Please then also create a letterhead to match the business card design

Colors

Designer to choose colors to be used in the design.

Requirements
Must have
• Must be a modern, elegant business card which looks very professional

```html
<!DOCTYPE html>
<html lang="en">
<head>
<meta charset="utf-8">
<title>Pimlu – Letterhead and Business Card</title>
<link href="https://fonts.googleapis.com/css2?family=Montserrat:wght@400;500;600;700&family=Open+Sans:wght@400&display=swap" rel="stylesheet">
<style>
  :root {
    --backdrop: #a3b5ba;
    --paper: #ffffff;
    --brand-red: #e30613;
    --ink: #3a3a3a;
    --rule: #555555;
    --card-dark: #2a2a2a;
    --card-mid: #3a3a3a;
    --card-text: #5e5e5e;
  }
  * { margin: 0; padding: 0; box-sizing: border-box; }
  html, body { width: 1200px; height: 900px; overflow: hidden; }
  body { background: var(--backdrop); position: relative; font-family: "Open Sans", sans-serif; }

  .letterhead {
    position: absolute; left: 109px; top: 86px; width: 570px; height: 728px;
    background: var(--paper); border-top: 3px solid var(--brand-red);
    box-shadow: 0 1px 4px rgba(0,0,0,.25);
  }
  .letterhead__brand {
    position: absolute; left: 0; right: 0; top: 12px; text-align: center;
    font-family: "Montserrat", sans-serif; font-weight: 700; font-size: 30px;
    letter-spacing: 1px; color: var(--brand-red);
  }
  .letterhead__rule { position: absolute; left: 44px; width: 482px; height: 1px; background: var(--rule); }
  .letterhead__rule--top { top: 51px; }
  .letterhead__rule--bottom { top: 680px; }

  .letter { position: absolute; left: 63px; top: 198px; width: 445px; color: var(--ink); font-size: 9.6px; line-height: 23px; }
  .letter__date { margin-bottom: 18px; }
  .letter p { margin-bottom: 4px; white-space: nowrap; overflow: hidden; }

  .signoff { position: absolute; left: 397px; top: 512px; color: var(--ink); font-size: 9.4px; line-height: 11px; }
  .signoff__signature { width: 110px; height: 34px; margin-bottom: 5px; border-radius: 3px;
    background: linear-gradient(90deg, #f2f2f2, #e6e6e6); }

  .contact-icons { position: absolute; left: 266px; top: 674px; display: flex; gap: 2px; background: var(--paper); padding: 0 2px; }
  .contact-icons svg { display: block; }

  .contact-line {
    position: absolute; left: 0; right: 0; top: 689px; text-align: center;
    font-family: "Montserrat", sans-serif; font-size: 9.6px; color: #222; word-spacing: 2px;
  }
  .contact-line span { margin: 0 5px; }
  .address-band {
    position: absolute; left: 0; right: 0; bottom: 0; height: 18px; background: var(--brand-red);
    color: #fff; text-align: center; font-family: "Montserrat", sans-serif; font-size: 9.4px; line-height: 18px;
  }

  .card { position: absolute; left: 710px; width: 381px; height: 217px; box-shadow: 0 1px 3px rgba(0,0,0,.3); }
  .card--pattern { top: 346px; border: 1px solid var(--brand-red); border-bottom-width: 2px; }
  .card__texture {
    position: absolute; inset: 0;
    background: linear-gradient(90deg, #1e1e1e 0%, #2d2d2d 35%, #4a4a4a 70%, #5c5c5c 100%);
  }
  .card__name {
    position: absolute; left: 231px; top: 162px;
    font-family: "Montserrat", sans-serif; font-weight: 700; font-size: 15px; letter-spacing: .5px;
    color: var(--brand-red);
  }
  .card--plain { top: 597px; background: linear-gradient(100deg, var(--card-dark), var(--card-mid)); border: 1px solid #4a2a2a; }
  .card__wordmark {
    position: absolute; left: 0; right: 0; top: 78px; text-align: center;
    font-family: "Montserrat", sans-serif; font-weight: 700; font-size: 46px; letter-spacing: 2px;
    color: var(--card-text);
  }
</style>
</head>
<body>

<section class="letterhead">
  <div class="letterhead__brand">Pimlu</div>
  <div class="letterhead__rule letterhead__rule--top"></div>

  <article class="letter">
    <div class="letter__date">Date, 10 September, 2020</div>
    <p>This is a sample letter that has been placed to demonstrate typing remat (Your Company). letterhead<br>design. When positioned properly, it will serve to work in harmony with all other elements letterhead.<br>This letterhead design is meant to project an image</p>
    <p>This letterhead design is meant project an image of professionalism reliability. By using simple aligen<br>we have created a very spacious feeling. The simplicity suggest&nbsp; rengththe spaciousnes contributes h<br>aesthetics the layout. These basic qualities along with the (Your Company)</p>
    <p>look and helps reinforce the (Your Company) brand. letterhead design is meant to project an image p<br>design. When positioned properly, it will serve to work in harmony all the other elements letterhead.<br>sionalism and reliability.</p>
    <p>This letterhead design is based on the (Form of your logo) form (Your Company) logo. Each stationery<br>we have created a very spacious feeling. The simplicity suggests strength the spaciousnes contribute<br>part of the (Form of your logo).</p>
  </article>

  <div class="signoff">
    <div class="signoff__signature" role="img" aria-label="Handwritten signature of Evan Hollis"></div>
    <div>Evan Hollis</div>
    <div>Manager</div>
  </div>

  <div class="letterhead__rule letterhead__rule--bottom"></div>
  <div class="contact-icons" aria-hidden="true">
    <svg width="11" height="11" viewBox="0 0 11 11"><circle cx="5.5" cy="5.5" r="5.5" fill="#e30613"/><path d="M3.4 2.8c.3-.3.7-.3.9 0l.6.8c.2.3.1.6-.1.8l-.3.3c.3.7.9 1.3 1.6 1.6l.3-.3c.2-.2.5-.3.8-.1l.8.6c.3.2.3.6 0 .9l-.4.4c-.4.4-1 .4-1.5.2-1.3-.6-2.4-1.7-3-3-.2-.5-.2-1.1.2-1.5z" fill="#fff"/></svg>
    <svg width="11" height="11" viewBox="0 0 11 11"><circle cx="5.5" cy="5.5" r="5.5" fill="#e30613"/><rect x="2.8" y="3.6" width="5.4" height="3.8" fill="none" stroke="#fff" stroke-width=".8"/><path d="M2.8 3.6l2.7 2 2.7-2" fill="none" stroke="#fff" stroke-width=".8"/></svg>
    <svg width="11" height="11" viewBox="0 0 11 11"><circle cx="5.5" cy="5.5" r="5.5" fill="#e30613"/><circle cx="5.5" cy="5.5" r="2.7" fill="none" stroke="#fff" stroke-width=".8"/><path d="M2.8 5.5h5.4M5.5 2.8c-1.2 1.5-1.2 3.9 0 5.4M5.5 2.8c1.2 1.5 1.2 3.9 0 5.4" fill="none" stroke="#fff" stroke-width=".6"/></svg>
  </div>
  <div class="contact-line"><span>0400 555 218</span><span>nora@pimlu.com</span><span>www.pimlu.com</span></div>
  <div class="address-band">PO Box 1180, Larkfield NSW 2690</div>
</section>

<section class="card card--pattern">
  <div class="card__texture" role="img" aria-label="Dark tonal repeating brand name texture"></div>
  <div class="card__name">Pimlu</div>
</section>

<section class="card card--plain">
  <div class="card__wordmark">Pimlu</div>
</section>

</body>
</html>
```